Professional Single Page Website Design for Tollbrook Advisory

Tollbrook Advisory is a new business consultancy specializing in providing expert services to small businesses, primarily in the brick-and-mortar retail and food service sectors. We offer a range of services including franchise development and launch, due diligence, and construction management.

Currently, we have a basic website set up at www.tollbrookadvisory.example, but we need a professional touch to enhance its design and functionality.

Project Requirements:
- Single Page Design: For now, we need a single page design that effectively showcases who we are, our services, and contact information.
- Future Expansion: The design should be flexible and scalable for future expansion to include additional pages like specific service offerings, about us, and a dedicated contact page.
- Design Aesthetic: We are looking for a modern yet professional design that aligns with our brand identity.
- Logo: We have a logo that we like, which was also sourced from Pixel Bazaar. The logo files are attached to this project brief.

Key Sections to Include:
- Hero Section: An engaging introduction to Tollbrook Advisory with a strong visual impact.
- About Us: A brief overview of who we are and our mission.
- Team: Section for the profiles of the two principals.
- Services: A clear and concise presentation of our services, including franchise development, due diligence, and construction management.
- Contact Information: Easy-to-find contact details, including a form for inquiries.
- Call to Action: Encouraging visitors to get in touch with us for consultations or further information.

Design Considerations:
- Ensure the design is responsive and mobile-friendly.
- Include high-quality images and icons that complement our services and industry.
- We do not need development services, this is only a design project.

```html
<!DOCTYPE html>
<html lang="en">
<head>
<meta charset="utf-8">
<title>Tollbrook Advisory</title>
<link href="https://fonts.googleapis.com/css2?family=Poppins:wght@400;500;600;700;800&display=swap" rel="stylesheet">
<style>
:root{
  --navy:#1f2b37;
  --navy-deep:#17212b;
  --mint:#8ecaaf;
  --mint-dark:#5f9e84;
  --mint-pale:#e9f3ef;
  --ink:#2a2f35;
  --muted:#6b7178;
  --white:#ffffff;
  --field:#fafafa;
}
*{margin:0;padding:0;box-sizing:border-box}
html,body{width:1200px;height:4392px;overflow:hidden}
body{font-family:'Poppins',sans-serif;color:var(--ink);background:var(--white);position:relative}
.abs{position:absolute}
/* hero */
.hero{left:0;top:0;width:1200px;height:767px;background:linear-gradient(180deg,#2e4a78 0%,#1d3358 45%,#132443 100%)}
.brand{display:flex;align-items:center;gap:10px;color:var(--white);font-weight:600}
.brand-dot{width:44px;height:44px;border-radius:50%;border:4px solid var(--mint)}
.nav{top:34px;left:612px;display:flex;gap:40px;font-size:15px;color:var(--white)}
.nav .active{color:var(--mint)}
.nav-line{top:92px;left:590px;width:490px;height:1px;background:rgba(255,255,255,.35)}
.hero-title{top:200px;width:1200px;text-align:center;color:var(--white);font-weight:800;font-size:50px;line-height:56px}
.hero-copy{top:330px;left:330px;width:540px;text-align:center;color:var(--white);font-size:14.5px;line-height:19.5px}
.btn{background:var(--mint);color:var(--white);font-weight:600;font-size:12px;display:flex;align-items:center;justify-content:center;border-radius:20px;letter-spacing:.3px}
.hero-btn{top:453px;left:523px;width:154px;height:38px}
.dots{top:604px;left:556px;display:flex;gap:16px}
.dots span{width:11px;height:11px;border-radius:50%;background:var(--white)}
.dots span.on{box-shadow:0 0 0 3px rgba(255,255,255,.5)}
/* section titles */
.sec-title{width:1200px;text-align:center;font-size:36px;font-weight:700;color:var(--ink)}
.sec-title em{font-style:normal;color:var(--mint)}
.mark{width:30px;height:30px;border-radius:50%;border:3px solid var(--mint);left:585px}
/* services */
.card{width:293px;height:510px;background:var(--white);box-shadow:0 6px 24px rgba(0,0,0,.09);top:980px}
.card h3{font-size:14.5px;font-weight:500;text-align:center;margin-top:30px}
.card p{font-size:10.5px;line-height:17.5px;color:var(--muted);text-align:center;padding:0 24px;margin-top:10px}
.card .down{width:26px;height:26px;margin:14px auto 0;display:block}
.card svg.pic{position:absolute;left:0;top:210px}
.arrow{width:32px;height:32px;border-radius:50%;background:var(--mint-dark);top:1189px;display:flex;align-items:center;justify-content:center}
.dots-band{background:rgba(31,43,55,.05)}
/* about */
.about{left:0;top:1625px;width:1200px;height:625px;background:var(--navy)}
.about h2{top:95px;left:663px;font-size:36px;line-height:41px;color:var(--white);font-weight:700}
.about h2 em{font-style:normal;color:var(--mint)}
.about .copy{top:190px;left:663px;width:410px;color:var(--white);font-size:11.8px;line-height:19px}
.about .copy p{margin-bottom:9px}
/* team */
.person h4{font-size:21px;font-weight:500}
.person .role{color:var(--mint);font-size:16.5px;margin-top:2px}
.person p{font-size:13px;line-height:20.5px;color:var(--muted);margin-top:16px}
/* contact */
.contact{left:0;top:3367px;width:1200px;height:686px;background:var(--mint-pale)}
.contact h3{left:128px;top:210px;font-size:34px;line-height:43px;font-weight:700;color:var(--ink)}
.ic{width:44px;height:44px;border-radius:10px;background:var(--mint-dark);transform:rotate(45deg) scale(.82);display:flex;align-items:center;justify-content:center}
.ic svg{transform:rotate(-45deg)}
.info{left:128px;font-size:13.5px;line-height:20px;color:var(--ink)}
.field{background:var(--field);border:1px solid #ececec;font-size:11.5px;color:var(--ink);padding-left:16px;display:flex;align-items:center}
.submit{left:478px;top:558px;width:327px;height:40px;border-radius:3px;font-size:10.5px;font-weight:700}
/* footer */
.footer{left:0;top:4053px;width:1200px;height:339px;background:var(--navy)}
.social{top:105px;display:flex;gap:8px;left:640px}
.social span{width:42px;height:42px;border-radius:50%;border:2px solid var(--white)}
.flinks{top:196px;width:1200px;text-align:center;color:var(--white);font-size:14px}
.copyr{top:250px;width:1200px;text-align:center;color:var(--white);font-size:14px}
</style>
</head>
<body>

<section class="abs hero" role="img" aria-label="Upward view of glass office towers against a blue sky">
</section>
<div class="abs brand" style="top:24px;left:136px;font-size:19px;line-height:20px">
  <span class="brand-dot"></span><span>Tollbrook<br>Advisory</span>
</div>
<nav class="abs nav">
  <span class="active">Home</span><span>About</span><span>Our Services</span><span>Team</span><span>Contact Us</span>
</nav>
<div class="abs nav-line"></div>
<h1 class="abs hero-title">Building Success<br>in Southern California</h1>
<p class="abs hero-copy">At Tollbrook, we blend innovative strategies with local market expertise to guide your commercial real estate ventures. Whether you're launching a new restaurant, investing in retail spaces, or expanding a franchise, our dedicated team is here to turn your real estate aspirations into tangible success. Dive into a partnership that grows with you.</p>
<div class="abs btn hero-btn">LEARN MORE</div>
<div class="abs dots"><span></span><span class="on"></span><span></span><span></span></div>

<!-- services -->
<span class="abs mark" style="top:855px"></span>
<h2 class="abs sec-title" style="top:888px"><em>Our</em> Services</h2>

<div class="abs arrow" style="left:66px"><svg width="14" height="14" viewBox="0 0 14 14"><path d="M12 7H2M6 3L2 7l4 4" stroke="#fff" stroke-width="1.6" fill="none"/></svg></div>
<div class="abs arrow" style="left:1101px"><svg width="14" height="14" viewBox="0 0 14 14"><path d="M2 7h10M8 3l4 4-4 4" stroke="#fff" stroke-width="1.6" fill="none"/></svg></div>

<article class="abs card" style="left:130px">
  <h3>Franchise Development</h3>
  <p>At Tollbrook Advisory, our Franchise Development &amp; Launch service is designed to transform your successful business into a thriving franchise. We start by thoroughly evaluating your business model</p>
  <svg class="down" viewBox="0 0 26 26"><circle cx="13" cy="13" r="11" fill="none" stroke="#555" stroke-width="1.2"/><path d="M13 8v10M9 14l4 4 4-4" stroke="#555" stroke-width="1.2" fill="none"/></svg>
  <svg class="pic" width="293" height="300" viewBox="0 0 293 300" role="img" aria-label="Retail shopping and commerce icons glowing over a digital background">
    <defs><linearGradient id="g1" x1="0" y1="0" x2="1" y2="1"><stop offset="0" stop-color="#2d6f8a"/><stop offset="1" stop-color="#1b2f3e"/></linearGradient></defs>
    <path d="M146 0 Q165 0 180 16 L277 112 Q293 130 277 148 L180 282 Q146 318 112 282 L16 148 Q0 130 16 112 L112 16 Q127 0 146 0Z" fill="url(#g1)" stroke="#8ecaaf" stroke-width="3"/>
  </svg>
</article>
<article class="abs card" style="left:452px">
  <h3>Due Diligence</h3>
  <p>Tollbrook offers comprehensive evaluations tailored to your business needs. We meticulously assess franchise opportunities, business sales, and property transactions, identifying potential risks and liabilities to</p>
  <svg class="down" viewBox="0 0 26 26"><circle cx="13" cy="13" r="11" fill="none" stroke="#555" stroke-width="1.2"/><path d="M13 8v10M9 14l4 4 4-4" stroke="#555" stroke-width="1.2" fill="none"/></svg>
  <svg class="pic" width="293" height="300" viewBox="0 0 293 300" role="img" aria-label="Hand holding a magnifying glass over documents">
    <defs><linearGradient id="g2" x1="0" y1="0" x2="1" y2="1"><stop offset="0" stop-color="#3a3a3a"/><stop offset="1" stop-color="#d9d4cc"/></linearGradient></defs>
    <path d="M146 0 Q165 0 180 16 L277 112 Q293 130 277 148 L180 282 Q146 318 112 282 L16 148 Q0 130 16 112 L112 16 Q127 0 146 0Z" fill="url(#g2)" stroke="#8ecaaf" stroke-width="3"/>
  </svg>
</article>
<article class="abs card" style="left:775px">
  <h3>Construction Management</h3>
  <p>Our Building &amp; Construction Management Services oversee every aspect of your construction and development projects, from initial planning to final completion. We ensure projects stay on time and within budget,</p>
  <svg class="down" viewBox="0 0 26 26"><circle cx="13" cy="13" r="11" fill="none" stroke="#555" stroke-width="1.2"/><path d="M13 8v10M9 14l4 4 4-4" stroke="#555" stroke-width="1.2" fill="none"/></svg>
  <svg class="pic" width="293" height="300" viewBox="0 0 293 300" role="img" aria-label="Two engineers in hard hats reviewing plans at a construction site">
    <defs><linearGradient id="g3" x1="0" y1="0" x2="0" y2="1"><stop offset="0" stop-color="#c9d3dc"/><stop offset="1" stop-color="#6b6a62"/></linearGradient></defs>
    <path d="M146 0 Q165 0 180 16 L277 112 Q293 130 277 148 L180 282 Q146 318 112 282 L16 148 Q0 130 16 112 L112 16 Q127 0 146 0Z" fill="url(#g3)" stroke="#8ecaaf" stroke-width="3"/>
  </svg>
</article>

<div class="abs dots-band" style="left:310px;top:1590px;width:890px;height:30px"></div>

<!-- about -->
<section class="abs about">
  <svg class="abs" style="left:130px;top:93px" width="445" height="447" viewBox="0 0 445 447" role="img" aria-label="Team of colleagues talking and smiling in an office">
    <defs><linearGradient id="g4" x1="0" y1="0" x2="1" y2="1"><stop offset="0" stop-color="#c8b8a4"/><stop offset="1" stop-color="#6b5a48"/></linearGradient></defs>
    <path d="M222 0 Q250 0 272 22 L423 173 Q445 198 423 223 L272 425 Q222 470 172 425 L22 223 Q0 198 22 173 L172 22 Q195 0 222 0Z" fill="url(#g4)"/>
  </svg>
  <h2 class="abs"><em>About</em> Tollbrook<br>Advisory</h2>
  <div class="abs copy">
    <p>Welcome to Tollbrook Advisory, your trusted partner in navigating the complexities of the real estate and small business markets. Founded by industry veterans Daniel Ortiz and Kevin Han, we specialize in providing comprehensive services tailored to the unique needs of our clients. Whether you're a franchisee, a new restaurant owner, or a commercial real estate investor, our expertise in due diligence, construction management, and investment property evaluation ensures you make informed, strategic decisions.</p>
    <p>At Tollbrook Advisory, we are committed to your success. Our approach combines meticulous analysis, strategic insights, and personalized service to help you achieve your business goals. We pride ourselves on our ability to deliver results that exceed expectations, fostering long-term relationships built on trust and excellence.</p>
    <p>Discover how Tollbrook Advisory can support your business journey. Partner with us and experience the difference our dedication and expertise can make.</p>
  </div>
</section>
<div class="abs dots-band" style="left:0;top:2252px;width:890px;height:30px"></div>

<!-- team -->
<span class="abs mark" style="top:2362px"></span>
<h2 class="abs sec-title" style="top:2400px"><em>Our</em> Leadership Team</h2>

<div class="abs person" style="left:131px;top:2543px;width:490px">
  <h4>Daniel Ortiz</h4>
  <div class="role">Principal</div>
  <p>Daniel Ortiz brings almost 20 years of rich experience as a real estate investor and a pivotal role at one of southern California's largest real estate management firms, where he led sales and marketing strategies to elevate property value and investor returns. His vast expertise spans through strategic development and market analysis, making him a cornerstone for Tollbrook Advisory.</p>
  <p style="margin-top:12px">Daniel's leadership and deep market understanding assure clients of unmatched guidance in their real estate investments, promising a partnership that drives value and innovation in every venture. Join us in transforming real estate opportunities into lasting achievements.</p>
</div>
<svg class="abs" style="left:712px;top:2505px" width="348" height="375" viewBox="0 0 348 375" role="img" aria-label="Portrait of Daniel Ortiz with a city view behind">
  <defs><linearGradient id="g5" x1="0" y1="0" x2="0" y2="1"><stop offset="0" stop-color="#b7c7d6"/><stop offset="1" stop-color="#e6e4e6"/></linearGradient></defs>
  <path d="M174 0 Q196 0 214 20 L330 148 Q348 170 330 192 L214 352 Q174 395 134 352 L18 192 Q0 170 18 148 L134 20 Q152 0 174 0Z" fill="url(#g5)" stroke="#8ecaaf" stroke-width="3"/>
</svg>

<svg class="abs" style="left:130px;top:2902px" width="348" height="375" viewBox="0 0 348 375" role="img" aria-label="Portrait of Kevin Han">
  <defs><linearGradient id="g6" x1="0" y1="0" x2="0" y2="1"><stop offset="0" stop-color="#8a7a6a"/><stop offset="1" stop-color="#2c2a2a"/></linearGradient></defs>
  <path d="M174 0 Q196 0 214 20 L330 148 Q348 170 330 192 L214 352 Q174 395 134 352 L18 192 Q0 170 18 148 L134 20 Q152 0 174 0Z" fill="url(#g6)" stroke="#8ecaaf" stroke-width="3"/>
</svg>
<div class="abs person" style="left:608px;top:2940px;width:465px">
  <h4>Kevin Han</h4>
  <div class="role">Principal</div>
  <p>Kevin Han is a seasoned real estate expert with extensive experience in project and construction management, and a licensed real estate agent in California. Fluent in both English and Korean, he specializes in commercial real estate, bringing invaluable expertise to Tollbrook Advisory.</p>
  <p style="margin-top:12px">His affiliation with the Regional Property Brokers Guild and the Retail Centers Alliance underscores his commitment to excellence and industry standards. Kevin's strategic insight and leadership in real estate development ensure clients receive strategic, value-driven solutions for their investments.</p>
</div>

<!-- contact -->
<section class="abs contact">
  <span class="abs mark" style="top:88px"></span>
  <h2 class="abs sec-title" style="top:123px">Contact <em>Us</em></h2>
  <h3 class="abs">Get In Touch With<br>Us Tollbrook<br>Advisory</h3>
  <div class="abs ic" style="left:128px;top:378px"><svg width="20" height="20" viewBox="0 0 20 20"><path d="M10 2a6 6 0 0 0-6 6c0 4.5 6 10 6 10s6-5.5 6-10a6 6 0 0 0-6-6z" fill="#1f2b37"/><circle cx="10" cy="8" r="2.2" fill="#5f9e84"/></svg></div>
  <div class="abs info" style="top:427px">218 Harbor View Rd Suite<br>40, CA 90000</div>
  <div class="abs ic" style="left:128px;top:485px"><svg width="20" height="20" viewBox="0 0 20 20"><path d="M5 2l3 3-2 2.5c1 2 2.5 3.5 4.5 4.5L13 10l3 3-2 3C8 15.5 4.5 12 4 6z" fill="#1f2b37"/></svg></div>
  <div class="abs info" style="top:536px">Phone +1 555 010 2040</div>

  <div class="abs field" style="left:478px;top:218px;width:288px;height:40px">First name</div>
  <div class="abs field" style="left:782px;top:218px;width:287px;height:40px">Last name</div>
  <div class="abs field" style="left:478px;top:275px;width:591px;height:40px">Phone</div>
  <div class="abs field" style="left:478px;top:335px;width:591px;height:40px">Email address</div>
  <div class="abs field" style="left:478px;top:394px;width:591px;height:40px">Company</div>
  <div class="abs field" style="left:478px;top:455px;width:591px;height:73px;align-items:flex-start;padding-top:16px">Tell me something about you*</div>
  <div class="abs btn submit">GET IN TOUCH WITH US FOR CONSULTATIONS</div>
</section>

<!-- footer -->
<footer class="abs footer">
  <div class="abs brand" style="left:318px;top:80px;font-size:31px;line-height:32px;gap:16px">
    <span class="brand-dot" style="width:70px;height:70px;border-width:6px"></span><span>Tollbrook<br>Advisory</span>
  </div>
  <div class="abs social"><span></span><span></span><span></span><span></span><span></span></div>
  <div class="abs flinks">About &nbsp;|&nbsp; Services &nbsp;|&nbsp; Team &nbsp;|&nbsp; Contact</div>
  <div class="abs copyr">Tollbrook Advisory © 2024. All Rights Reserved.</div>
</footer>

</body>
</html>
```